Business Card Design for company

We want new business cards. We'd like something different-- yet still highly professional. Our tagline is Providing leadership, delivering success. Stock photos are ok, as long as they are relevant and look upscale.

Target Market(s)

Architecture/Business Management Consulting/Engineering Consulting

Contact Information for Business Card

dark gray background with pops of blue might be good, but you tell me. You're the designers. Rounded corners might be nice, but again, you tell me.

Font styles to use
Serif
Sans Serif

Colors
3276b5
5c5c5c
9d9d9d
fbfbfb

Requirements
Nice to have
• Something different, but still very professional.

```html
<!DOCTYPE html>
<html lang="en">
<head>
<meta charset="utf-8">
<title>Veltra Global — Business Card</title>
<link rel="stylesheet" href="https://fonts.googleapis.com/css2?family=Montserrat:wght@400;500;600;700&family=Arimo:wght@400&display=swap">
<style>
  :root {
    --stage: #cbbfc6;
    --card: #0b0b0d;
    --map: #1c1d21;
    --blue: #3276b5;
    --grey: #9d9d9d;
    --mid-grey: #5c5c5c;
    --white: #fbfbfb;
  }
  * { box-sizing: border-box; margin: 0; padding: 0; }
  html, body { width: 1200px; height: 1200px; overflow: hidden; }
  body {
    background: var(--stage);
    font-family: "Montserrat", sans-serif;
    display: flex;
    flex-direction: column;
    align-items: center;
    justify-content: center;
    gap: 60px;
  }
  .card {
    position: relative;
    width: 840px;
    height: 502px;
    background: var(--card);
    border-radius: 22px;
    overflow: hidden;
    box-shadow: 0 8px 18px rgba(0,0,0,.35);
  }
  .world-map {
    position: absolute;
    inset: 30px 40px 40px 40px;
    border-radius: 40%;
    background: radial-gradient(ellipse at 50% 45%, var(--map) 0%, rgba(28,29,33,.6) 45%, rgba(11,11,13,0) 75%);
  }
  .brand-name {
    font-family: "Montserrat", sans-serif;
    font-weight: 500;
    color: var(--grey);
    text-align: center;
    line-height: 1.05;
    letter-spacing: .04em;
  }

  /* front */
  .card--front .brand-name {
    position: absolute;
    left: 0; right: 0; top: 150px;
    font-size: 84px;
  }
  .tagline {
    position: absolute;
    left: 0; right: 0; bottom: 40px;
    text-align: center;
    color: var(--white);
    font-size: 19px;
    font-weight: 500;
    letter-spacing: .1em;
  }

  /* back */
  .card--back .brand-name {
    position: absolute;
    left: 40px; width: 380px; top: 158px;
    font-size: 46px;
  }
  .divider {
    position: absolute;
    left: 436px; top: 135px;
    width: 2px; height: 200px;
    background: var(--grey);
  }
  .contact {
    position: absolute;
    left: 472px; top: 135px;
    color: var(--white);
  }
  .contact__name { font-size: 32px; font-weight: 600; letter-spacing: .06em; }
  .contact__title { font-size: 20px; font-weight: 500; margin-top: 4px; letter-spacing: .03em; }
  .contact__list { list-style: none; margin-top: 20px; }
  .contact__list li {
    display: flex; align-items: center; gap: 12px;
    font-size: 18.5px; line-height: 27px; font-weight: 400;
  }
  .contact__list svg { width: 13px; height: 13px; flex: none; }
  .address-band {
    position: absolute;
    left: 0; right: 0; bottom: 0;
    height: 64px;
    background: var(--blue);
    border-top: 3px solid #1a4f80;
    display: flex; align-items: center; justify-content: center;
    font-family: "Arimo", sans-serif;
    font-size: 22px;
    color: var(--white);
    letter-spacing: -.02em;
  }
  .address-band::before {
    content: "";
    position: absolute;
    left: 0; right: 0; top: -10px;
    height: 2px;
    background: var(--blue);
  }
</style>
</head>
<body>
  <section class="card card--front" aria-label="Business card front">
    <div class="world-map" role="img" aria-label="Faint world map silhouette in dark grey"></div>
    <div class="brand-name">VELTRA<br>GLOBAL</div>
    <p class="tagline">PROVIDING LEADERSHIP | DELIVERING SUCCESS</p>
  </section>

  <section class="card card--back" aria-label="Business card back">
    <div class="world-map" role="img" aria-label="Faint dotted world map in dark grey"></div>
    <div class="brand-name">VELTRA<br>GLOBAL</div>
    <div class="divider"></div>
    <div class="contact">
      <h1 class="contact__name">EVAN HOLLOWAY</h1>
      <p class="contact__title">Design Consultant</p>
      <ul class="contact__list">
        <li><svg viewBox="0 0 16 16" fill="var(--white)"><path d="M3.5 1l2.5 3-1.5 2c1 2 3 4 5 5l2-1.5 3 2.5-1.5 2.5C8 14 2 8 1 2.5z"/></svg>+1 555-010-2846</li>
        <li><svg viewBox="0 0 16 16" fill="none" stroke="var(--white)" stroke-width="1.8"><rect x="1.5" y="3" width="13" height="10"/><path d="M1.5 3l6.5 6 6.5-6"/></svg>MARKETING@VELTRAGLOBAL.COM</li>
        <li><svg viewBox="0 0 16 16" fill="none" stroke="var(--white)" stroke-width="1.8"><rect x="1.5" y="3" width="13" height="10"/><path d="M1.5 3l6.5 6 6.5-6"/></svg>HELLO@VELTRAGLOBAL.COM</li>
        <li><svg viewBox="0 0 16 16" fill="none" stroke="var(--white)" stroke-width="1.5"><circle cx="8" cy="8" r="6.5"/><ellipse cx="8" cy="8" rx="2.8" ry="6.5"/><path d="M1.5 8h13"/></svg>www.veltraglobal.com</li>
      </ul>
    </div>
    <div class="address-band">418 Harbor Crest Lane Tampa, FL 33602</div>
  </section>
</body>
</html>
```